Web-Design  für naturwissenschaflich-philosophische Institution
Web-Design für naturwissenschaflich-philosophische Institution
Zielgruppe
Es handelt sich um eine naturwissenschaflich-philosophische Institution. Besucher sind neben Natur- und Geisteswissenschaftlern auch interessierte Laien.
Kernthema der Seite ist alles rund um das Thema Zahlen, allerdings unter einem naturwissenschaftlich, philosophischen Aspekt. Nach einer grundsätzlichen Erklärung (Leitartikel 'Wozu Formen führen') baut die Seite sich auf aus zahreichen Beispielen/Beiträgen aus den unterschiedlichsten Fachbereichen, die scheinbar keinerlei Bezug zueinander haben, wie Mathematik, Geometrie einerseits und der großen Literatur einschließlich historischer und religiöser Schriften andererseits. Immer aber gibt es einen Bezug zu fraktal wachsenden Dreiecken.
Die Artikel sind meist populärwissenschaftlich formuliert. Es handelt sich nicht um esoterische Inhalte, auch wenn der Domainname www.tafelgrund.de das evtl. vermuten ließe. Keine Berührung zu Spiritualität. Die Institution ist im Aufbau und hat durchaus den Anspruch, diese klassischen Themen modern aufzugreifen. Sie ist nicht verstaubt.
Aufgabenstellung
Geordneter, klarer, transparenter Aufbau. Übersichtlich und strukturiert, wie zB www.kvt.de Es sollten geometrische Proportionen eingehalten werden (wie Symmetrie, goldener Schnitt). Nicht zu viele verschiedene Stilelemente. Die Seite sollte einladend sein, ggf. ansprechendes Bild auf Startseite (mit Bezug zu Zahlen, Geoemetrie).
Die Startseite braucht nun im Header kein Logo mehr zu haben. Der Seitentitel sollte sein 'Das Gefüge der Linien'. Siehe Anhang 'Header Beispiel'
Als Menüpunkte benötigen wir neben Home, nur 'Beiträge', 'Buch', 'Kontakt' oder einfach nur die bekannten drei Striche. Der Link zum Impressum genügt im Footer. Rechts oben benötigt man ein Suchfeld.
Besonderheit: Man benötigt eine Art zweiten Header, der aus einer Zahlenreihe besteht. Die einzelnen Zahlen müssen später verlinkt sein auf Unterseiten. Siehe Muster im Anhang. Der User muss sie als Link erkennen können (evtl. Programmierthema: zB Hervorheben beim drüberhoovern). Die Zahlen müssen erweiterbar sein, ggf. über Pfeil klicken, siehe
Es gibt einen zentralen Startartikel. Auf diesen muss man leicht kommen. Im Muster heißt er 'Wozu die Formen führen'.
Das Bild hier ist sehr wichtig. Es sollte bestehn aus vielen interessanten Zahlen, wie in 'Zahlenwolke' angegeben. Und möglichst auch den Dreiecken wie in 'Logo1'.
Weiter unten auf der Startseite sollte es dann weitere Elemente geben, einmal wo man zu bestimmten Unterkategorien kommt, im Muster sind das 'Bibel und Zahlen' 'Naturwissenschaft' etc. und dann evtl weiter unten noch ein Stilelemente, in welchem man die neuesten Artikel verlinken kann.

```html
<!DOCTYPE html>
<html lang="de">
<head>
<meta charset="utf-8">
<title>Das Gefüge der Linien</title>
<link href="https://fonts.googleapis.com/css2?family=Poppins:wght@400;500;600;700&display=swap" rel="stylesheet">
<style>
  :root {
    --blue: #1a82f0;
    --navy: #1f2d44;
    --text: #2f3a4a;
    --grey-bar: #efefef;
    --card: #f1f1f1;
    --white: #ffffff;
    --hero-top: #3a7db8;
    --hero-bottom: #4fc8ec;
  }
  * { box-sizing: border-box; margin: 0; padding: 0; }
  html, body { width: 1153px; height: 1200px; overflow: hidden; }
  body { font-family: "Poppins", sans-serif; background: var(--white); position: relative; color: var(--text); }

  .site-header { position: absolute; left: 0; top: 0; width: 1153px; height: 60px; background: var(--white); box-shadow: 0 1px 4px rgba(0,0,0,0.08); z-index: 2; }
  .site-title { position: absolute; left: 168px; top: 16px; font-size: 21px; font-weight: 500; color: var(--blue); letter-spacing: 0.2px; }
  .site-title strong { font-weight: 600; }
  .main-nav { position: absolute; left: 520px; top: 23px; display: flex; align-items: center; font-size: 10.5px; font-weight: 500; color: var(--navy); letter-spacing: 0.3px; }
  .main-nav a { color: inherit; text-decoration: none; }
  .main-nav .sep { width: 1px; height: 9px; background: #c9c9c9; margin: 0 12px; }
  .main-nav .active { color: var(--blue); border-bottom: 2px solid var(--blue); padding-bottom: 3px; margin-top: 5px; }
  .search { position: absolute; left: 864px; top: 18px; width: 121px; height: 24px; border: 1px solid #9aa0a8; border-radius: 3px; }
  .search span { position: absolute; left: 6px; top: 5px; font-size: 10px; color: #d5d5d5; }
  .search svg { position: absolute; right: 6px; top: 5px; }

  .number-bar { position: absolute; left: 0; top: 60px; width: 1153px; height: 36px; background: var(--grey-bar); }
  .number-bar .label { position: absolute; right: 438px; top: 10px; font-size: 10.5px; font-weight: 500; color: var(--navy); }
  .number-bar .arrow { position: absolute; top: 13px; }
  .number-list { position: absolute; left: 757px; top: 9px; display: flex; gap: 6px; }
  .number-list a { width: 18px; height: 18px; border-radius: 3px; background: var(--navy); color: var(--white); font-size: 12px; font-weight: 600; text-align: center; line-height: 18px; text-decoration: none; }
  .number-list a.current { background: var(--blue); }

  .hero { position: absolute; left: 0; top: 96px; width: 1153px; height: 504px; background: linear-gradient(170deg, var(--hero-top) 0%, #4a9fd8 50%, var(--hero-bottom) 100%); }
  .hero h1 { position: absolute; left: 168px; top: 148px; font-size: 55px; line-height: 60px; font-weight: 700; color: var(--white); letter-spacing: -0.5px; }
  .hero .btn-light { position: absolute; left: 168px; top: 305px; width: 220px; height: 36px; background: #f0f0f0; color: var(--blue); font-size: 11px; font-weight: 500; text-align: center; line-height: 36px; text-decoration: none; }

  .categories { position: absolute; left: 168px; top: 690px; display: flex; gap: 23px; }
  .card { position: relative; width: 257px; height: 300px; background: var(--card); box-shadow: 0 2px 5px rgba(0,0,0,0.12); padding: 26px 25px 0; }
  .card h2 { font-size: 28px; line-height: 33px; font-weight: 600; color: var(--navy); height: 88px; }
  .card p { margin-top: 3px; font-size: 10.8px; line-height: 15.6px; color: var(--text); }
  .card .btn { position: absolute; left: 25px; top: 240px; width: 134px; height: 36px; background: var(--blue); color: var(--white); font-size: 11px; font-weight: 500; text-align: center; line-height: 36px; text-decoration: none; }

  .to-top { position: absolute; left: 1045px; top: 1091px; width: 25px; height: 24px; background: #eeeeee; border-radius: 2px; }
  .to-top svg { position: absolute; left: 6px; top: 7px; }

  .site-footer { position: absolute; left: 0; top: 1138px; width: 1153px; height: 62px; background: #ededed; box-shadow: 0 -2px 4px rgba(0,0,0,0.04); }
</style>
</head>
<body>
  <header class="site-header">
    <div class="site-title"><strong>Das Gefüge</strong> der Linien</div>
    <nav class="main-nav">
      <a class="active" href="#">HOME</a><span class="sep"></span>
      <a href="#">BETRAGE</a><span class="sep"></span>
      <a href="#">BUCH</a><span class="sep"></span>
      <a href="#">KONTAKT</a><span class="sep"></span>
      <a href="#">IMPRESSUM</a>
    </nav>
    <div class="search">
      <span>Suche</span>
      <svg width="12" height="12" viewBox="0 0 12 12"><circle cx="7" cy="5" r="4" fill="none" stroke="#1f2d44" stroke-width="1.2"/><line x1="4.2" y1="7.8" x2="1" y2="11" stroke="#1f2d44" stroke-width="1.3"/></svg>
    </div>
  </header>

  <div class="number-bar">
    <span class="label">und was sie erzählen:</span>
    <svg class="arrow" style="left:739px" width="6" height="7" viewBox="0 0 6 7"><polygon points="6,0 6,7 0,3.5" fill="#1f2d44"/></svg>
    <div class="number-list">
      <a class="current" href="#">1</a><a href="#">2</a><a href="#">3</a><a href="#">4</a><a href="#">5</a><a href="#">6</a><a href="#">7</a><a href="#">8</a><a href="#">9</a>
    </div>
    <svg class="arrow" style="left:979px" width="6" height="7" viewBox="0 0 6 7"><polygon points="0,0 0,7 6,3.5" fill="#1a82f0"/></svg>
  </div>

  <section class="hero" role="img" aria-label="Blaue Zahlenwolke mit Ziffern, Linien und Dreiecken aus verschachtelten Zahlen">
    <h1>Wozu die<br>Formen führen ...</h1>
    <a class="btn-light" href="#">Lern mehr</a>
  </section>

  <section class="categories">
    <article class="card">
      <h2>Bibel und Zahlen</h2>
      <p>Die Heilige Schrift ist ein Werk aus Zahlen. Ihre Verfasser haben die archetypischen Inhalte in wundersamer Art und Weise in der Bibel. Und so weiter und so fort</p>
      <a class="btn" href="#">Lern mehr</a>
    </article>
    <article class="card">
      <h2>Naturwissens chaft</h2>
      <p>Die Heilige Schrift ist ein Werk aus Zahlen. Ihre Verfasser haben die archetypischen Inhalte in wundersamer Art</p>
      <a class="btn" href="#">Lern mehr</a>
    </article>
    <article class="card">
      <h2>Philosophie</h2>
      <p>Die Heilige Schrift ist ein Werk aus Zahlen. Ihre Verfasser haben die archetypischen Inhalte in wundersamer Art und Weise der Bibel. Und so weiter und so fort und vieles mehr das sehr schön eindrucksvoll ist</p>
      <a class="btn" href="#">Lern mehr</a>
    </article>
  </section>

  <a class="to-top" href="#"><svg width="13" height="11" viewBox="0 0 13 11"><polygon points="6.5,0 13,11 0,11" fill="#1f2d44"/></svg></a>

  <footer class="site-footer"></footer>
</body>
</html>
```